KRT Project Signage

Need a sign to be displayed in the front of properties currently under Construction or Renovation to advertise our company information. Need it to be Professional and Contemporary. We are a Design/Build Construction Company. Information should include Company Name, email, website, phone number. Attached: Logo and company brochure, also included and inspiration images

```html
<!DOCTYPE html>
<html lang="en">
<head>
<meta charset="utf-8">
<title>KRT Project Signage</title>
<link rel="stylesheet" href="https://fonts.googleapis.com/css2?family=Montserrat:wght@400;500;700;800;900&display=swap">
<style>
  :root {
    --backdrop: #b1adab;
    --sign-light: #ececec;
    --brand-yellow: #eeeb47;
    --ink: #0b0b0b;
    --white: #ffffff;
    --panel-dark: #0d0d0d;
  }
  * { box-sizing: border-box; margin: 0; padding: 0; }
  html, body { width: 1200px; height: 1200px; overflow: hidden; }
  body {
    background: var(--backdrop);
    font-family: "Montserrat", sans-serif;
    position: relative;
  }
  .sign {
    position: absolute;
    left: 232px; top: 50px;
    width: 742px; height: 1107px;
    overflow: hidden;
  }
  .sign-shapes { position: absolute; inset: 0; }
  .brand {
    position: absolute;
    left: 0; right: 0; top: 190px;
    display: flex; align-items: center; justify-content: center; gap: 18px;
  }
  .brand-dot {
    width: 44px; height: 44px; border-radius: 50%;
    background: var(--brand-yellow);
  }
  .brand-name {
    font-weight: 700; font-size: 46px; letter-spacing: 2px;
    color: var(--ink); text-transform: uppercase;
  }
  .tagline {
    position: absolute; left: 0; right: 0; top: 262px;
    text-align: center;
    font-weight: 500; font-size: 24px; letter-spacing: 4px;
    color: var(--ink); text-transform: uppercase;
  }
  .company-title {
    position: absolute; left: 0; right: 0; top: 586px;
    text-align: center;
    font-weight: 900; font-size: 59px; letter-spacing: 0.5px;
    color: var(--ink);
  }
  .contact-list {
    position: absolute; left: 60px; top: 680px;
    list-style: none;
  }
  .contact-item {
    display: flex; align-items: center; gap: 26px;
    font-size: 34px; font-weight: 500; color: var(--ink);
    height: 48px; margin-bottom: 12px;
  }
  .contact-icon { width: 36px; height: 36px; flex: none; }
  .phones {
    position: absolute; left: 0; right: 0; top: 855px; bottom: 0;
    color: var(--white);
  }
  .phone-line {
    position: absolute; left: 0; right: 0;
    text-align: center; font-size: 42px; font-weight: 500;
  }
  .phone-line strong { font-weight: 700; }
  .phone-direct { top: 45px; }
  .phone-office { top: 148px; }
  .phone-divider {
    position: absolute; left: 94px; width: 553px; top: 121px;
    height: 5px; background: var(--brand-yellow);
  }
</style>
</head>
<body>
  <main class="sign">
    <svg class="sign-shapes" viewBox="0 0 742 1107" width="742" height="1107" aria-hidden="true">
      <defs>
        <linearGradient id="panelSheen" x1="0" y1="0" x2="1" y2="1">
          <stop offset="0" stop-color="#1c1c1c"/>
          <stop offset="0.5" stop-color="#0a0a0a"/>
          <stop offset="1" stop-color="#1a1a1a"/>
        </linearGradient>
      </defs>
      <rect width="742" height="1107" fill="var(--sign-light)"/>
      <path d="M0 353 C200 470 380 545 470 541 C600 540 700 470 742 400 L742 1107 L0 1107 Z" fill="var(--ink)"/>
      <path d="M0 387 C200 490 380 530 470 524 C620 520 710 440 742 375 L742 1107 L0 1107 Z" fill="var(--brand-yellow)"/>
      <rect y="832" width="742" height="23" fill="var(--white)"/>
      <rect y="855" width="742" height="252" fill="url(#panelSheen)"/>
      <g stroke="#2a2a2a" stroke-width="14" opacity="0.5">
        <line x1="0" y1="960" x2="120" y2="855"/>
        <line x1="40" y1="1107" x2="330" y2="855"/>
        <line x1="420" y1="1107" x2="710" y2="855"/>
        <line x1="600" y1="1107" x2="742" y2="985"/>
      </g>
    </svg>

    <div class="brand">
      <span class="brand-dot"></span>
      <span class="brand-name">KRT Construction</span>
    </div>
    <p class="tagline">Luxury Renovations</p>

    <h1 class="company-title">KRT Construction</h1>

    <ul class="contact-list">
      <li class="contact-item">
        <svg class="contact-icon" viewBox="0 0 36 36" aria-hidden="true">
          <rect x="3" y="8" width="30" height="22" fill="none" stroke="var(--ink)" stroke-width="2.5"/>
          <path d="M3 10 L18 21 L33 10 M3 29 L14 18 M33 29 L22 18" fill="none" stroke="var(--ink)" stroke-width="2.5"/>
        </svg>
        <span>daniel@krtconstruction.com</span>
      </li>
      <li class="contact-item">
        <svg class="contact-icon" viewBox="0 0 36 36" aria-hidden="true">
          <circle cx="18" cy="18" r="15" fill="none" stroke="var(--ink)" stroke-width="3"/>
          <ellipse cx="18" cy="18" rx="6.5" ry="15" fill="none" stroke="var(--ink)" stroke-width="2.5"/>
          <path d="M3 18 H33 M6 10 H30 M6 26 H30" stroke="var(--ink)" stroke-width="2.5"/>
        </svg>
        <span>www.krtconstruction.com</span>
      </li>
    </ul>

    <section class="phones">
      <p class="phone-line phone-direct">Direct: <strong>555.210.4837</strong></p>
      <div class="phone-divider"></div>
      <p class="phone-line phone-office">Office: <strong>555.210.4900</strong></p>
    </section>
  </main>
</body>
</html>
```